Design needed for an A5 Flyer and Newspaper Ad

We are looking for a designer who can create us two graphical files. One is a flyer and one is a newspaper ad. Both have the same content. They just have a different format. Both the flyer and the ad should be in an adobe format.

Size:
Flyer format: A5
Newspaper format: 16 cm x 8 cm

We want you to create an ad and the flyer for gold purchase. I addes a file of a flyer from a competitor (1036 x 733.jpg). It can be made similar if you like. The file you make must be adjustable.

What needs to be on it:
Our Logo (Kessler Lindt AG)
Our address: Talweg 7, 4790 Tannried
Since 1931

Font styles to use
Sans Serif

```html
<!DOCTYPE html>
<html lang="de">
<head>
<meta charset="utf-8">
<title>Kessler Roth AG – Gold &amp; Silber Flyer A5</title>
<link rel="stylesheet" href="https://fonts.googleapis.com/css2?family=Cinzel:wght@600;700&family=Montserrat:ital,wght@0,400;0,500;0,600;0,700;0,800;1,400;1,500&display=swap">
<style>
  :root {
    --backdrop: #d4d4d4;
    --paper-top: #e4e4e4;
    --paper-bottom: #f7f7f7;
    --ink: #2b2b2b;
    --red: #e31b23;
    --navy: #2e3192;
    --grey-text: #7a7a7a;
    --frame: #b9b9b9;
    --gold-light: #f3d27a;
    --gold: #d6a63a;
    --gold-dark: #a8781c;
  }
  * { margin: 0; padding: 0; box-sizing: border-box; }
  html, body { width: 902px; height: 1200px; overflow: hidden; }
  body { background: var(--backdrop); font-family: "Montserrat", sans-serif; color: var(--ink); }

  .flyer {
    position: absolute; left: 41px; top: 20px; width: 820px; height: 1160px;
    background: linear-gradient(180deg, var(--paper-top) 0%, var(--paper-top) 55%, var(--paper-bottom) 86%, #fff 100%);
    box-shadow: 4px 6px 12px rgba(0,0,0,.25);
    overflow: hidden;
  }
  .intro {
    position: absolute; top: 51px; width: 100%; text-align: center;
    font-size: 43px; font-weight: 500; line-height: 52px; letter-spacing: .2px; color: var(--ink);
  }
  .headline {
    position: absolute; top: 114px; width: 100%; text-align: center;
    font-family: "Cinzel", serif; font-weight: 700; font-size: 84px; line-height: 1;
    color: var(--red); letter-spacing: -1.5px;
  }
  .headline .amp { color: var(--navy); font-weight: 600; }

  .values {
    position: absolute; top: 206px; width: 100%; display: flex; justify-content: center; gap: 18px;
    font-style: italic; font-size: 36px; font-weight: 400; color: var(--ink);
  }
  .values li { list-style: none; display: flex; align-items: center; gap: 10px; }
  .values svg { width: 28px; height: 28px; }

  .hero-coins {
    position: absolute; left: 143px; top: 305px; width: 532px; height: 310px;
    border-radius: 150px;
    background: radial-gradient(ellipse at 45% 40%, var(--gold-light) 0%, var(--gold) 55%, var(--gold-dark) 100%);
  }

  .gallery { position: absolute; top: 663px; left: 69px; display: flex; gap: 16px; }
  .gallery .photo {
    width: 216px; height: 116px; border: 2px solid var(--frame); background: #fff; padding: 5px;
  }
  .gallery .photo div { width: 100%; height: 100%;
    background: linear-gradient(135deg, #fff6dc 0%, var(--gold-light) 35%, var(--gold) 70%, #fff 100%); }

  .products {
    position: absolute; top: 804px; width: 100%; text-align: center;
    font-size: 26.5px; font-weight: 600; line-height: 43px; color: var(--ink);
  }
  .products .sep { color: var(--navy); font-weight: 400; padding: 0 5px; }

  .tagline {
    position: absolute; top: 910px; width: 100%; text-align: center;
    font-size: 21.5px; font-weight: 500; color: var(--navy);
  }

  .footer {
    position: absolute; left: 0; top: 1021px; width: 100%; height: 139px; background: #fff;
  }
  .rule { position: absolute; left: 0; top: 1015px; width: 703px; height: 6px; background: var(--navy); }

  .call {
    position: absolute; left: 38px; top: 1002px; width: 298px; height: 31px;
    background: var(--red); border: 2px solid #fff; outline: 1px solid var(--red);
    border-radius: 16px; color: #fff; font-weight: 700; font-size: 20.5px;
    display: flex; align-items: center; justify-content: center; letter-spacing: .3px;
  }

  .seal { position: absolute; left: 382px; top: 972px; width: 84px; height: 84px; }

  .brand {
    position: absolute; left: 520px; top: 1036px; display: flex; align-items: center; gap: 8px;
    font-weight: 800; font-size: 25px; color: var(--red); letter-spacing: .5px;
  }
  .brand .mark { width: 14px; height: 14px; background: var(--navy); }
  .since { position: absolute; right: 26px; top: 1088px; font-size: 14px; font-weight: 500; color: var(--ink); }

  .contact { position: absolute; left: 40px; top: 1052px; font-size: 17px; color: var(--ink); }
  .contact p { display: flex; align-items: center; gap: 18px; height: 28px; }
  .contact span { display: flex; align-items: center; gap: 6px; }
  .contact svg { width: 20px; height: 20px; }
  .note { position: absolute; left: 43px; top: 1114px; font-size: 12.4px; color: var(--grey-text); }
</style>
</head>
<body>
<main class="flyer">
  <p class="intro">wir suchen und kaufen</p>
  <h1 class="headline">GOLD <span class="amp">&amp;</span> SILBER</h1>

  <ul class="values">
    <li><svg viewBox="0 0 28 28"><circle cx="14" cy="14" r="11.5" fill="none" stroke="var(--red)" stroke-width="2.6"/><path d="M8 14l5 5 11-14" fill="none" stroke="var(--red)" stroke-width="2.8" stroke-linecap="round" stroke-linejoin="round"/></svg>Sicher</li>
    <li><svg viewBox="0 0 28 28"><circle cx="14" cy="14" r="11.5" fill="none" stroke="var(--red)" stroke-width="2.6"/><path d="M8 14l5 5 11-14" fill="none" stroke="var(--red)" stroke-width="2.8" stroke-linecap="round" stroke-linejoin="round"/></svg>Transparenz</li>
    <li><svg viewBox="0 0 28 28"><circle cx="14" cy="14" r="11.5" fill="none" stroke="var(--red)" stroke-width="2.6"/><path d="M8 14l5 5 11-14" fill="none" stroke="var(--red)" stroke-width="2.8" stroke-linecap="round" stroke-linejoin="round"/></svg>Fair</li>
  </ul>

  <div class="hero-coins" role="img" aria-label="Foto: Gruppe verschiedener Goldmünzen"></div>

  <div class="gallery">
    <div class="photo"><div role="img" aria-label="Foto: Goldschmuck, Ringe und Ketten"></div></div>
    <div class="photo"><div role="img" aria-label="Foto: Goldbarren mit Münzstapeln"></div></div>
    <div class="photo"><div role="img" aria-label="Foto: Haufen von Goldmünzen"></div></div>
  </div>

  <p class="products">
    Goldvreneli<span class="sep">|</span>Altgold und Silber<span class="sep">|</span>Münzen<span class="sep">|</span>Barren<br>
    Medaillen<span class="sep">|</span>Uhren<span class="sep">|</span>Ringe<span class="sep">|</span>Ketten
  </p>

  <p class="tagline">Durchsuchen Sie ihren Haushalt - es könnte sich lohnen!</p>

  <div class="footer"></div>
  <div class="rule"></div>

  <div class="call">CALL 0041 61 555 01 20</div>

  <svg class="seal" viewBox="0 0 84 84" aria-label="Sofort Bargeld">
    <defs>
      <radialGradient id="sealGold" cx="40%" cy="35%" r="70%">
        <stop offset="0" stop-color="#fbe7a6"/><stop offset=".6" stop-color="#d9a93c"/><stop offset="1" stop-color="#9c6f17"/>
      </radialGradient>
    </defs>
    <circle cx="42" cy="42" r="41" fill="url(#sealGold)"/>
    <circle cx="42" cy="42" r="33" fill="#fff"/>
    <circle cx="42" cy="42" r="29" fill="none" stroke="#d6a63a" stroke-width="1.2" stroke-dasharray="2 3"/>
    <g transform="rotate(-28 42 42)" font-family="Cinzel, serif" font-weight="700" font-size="10" fill="#222" text-anchor="middle">
      <text x="42" y="40">SOFORT</text>
      <text x="42" y="52">BARGELD</text>
    </g>
  </svg>

  <div class="brand"><span class="mark"></span>KESSLER ROTH AG</div>
  <p class="since">Since 1931</p>

  <div class="contact">
    <p><span><svg viewBox="0 0 20 20"><circle cx="10" cy="10" r="9" fill="none" stroke="var(--navy)" stroke-width="1.4"/><path d="M10 4.5a3.6 3.6 0 0 0-3.6 3.6c0 2.7 3.6 7 3.6 7s3.6-4.3 3.6-7A3.6 3.6 0 0 0 10 4.5z" fill="var(--navy)"/><circle cx="10" cy="8.1" r="1.3" fill="#fff"/></svg>Talweg 7, 4790 Tannried</span></p>
    <p>
      <span><svg viewBox="0 0 20 20"><circle cx="10" cy="10" r="9" fill="none" stroke="var(--navy)" stroke-width="1.4"/><circle cx="10" cy="10" r="5.5" fill="none" stroke="var(--navy)" stroke-width="1.1"/><ellipse cx="10" cy="10" rx="2.3" ry="5.5" fill="none" stroke="var(--navy)" stroke-width="1.1"/><path d="M4.5 10h11" stroke="var(--navy)" stroke-width="1.1"/></svg>www.kessler-roth.ch</span>
      <span><svg viewBox="0 0 20 20"><circle cx="10" cy="10" r="9" fill="none" stroke="var(--navy)" stroke-width="1.4"/><rect x="5" y="6.5" width="10" height="7" rx="1" fill="var(--navy)"/><path d="M5.5 7l4.5 3.5L14.5 7" fill="none" stroke="#fff" stroke-width="1"/></svg>info@kessler-roth.ch</span>
    </p>
  </div>
  <p class="note">Wir sind seit über 90 Jahren im Handel mit Briefmarken und Münzen tätig.</p>
</main>
</body>
</html>
```